International business needs business cards

Our company, DRV Ventures Inc. is in the business of supplying a range construction products with particular emphasis on CEMENT. We have developed our own brand - TORVAN SUPPLIES - with which to infiltrate the market. We are launching our brand of cement (TORVAN Type IS Cement) into the Caribbean which is unlike anything this market has ever seen. A monopoly has existed here for the past 60-odd years and the market has now opened to allow the importation of other brands and consumers are anxious and ready for change/improvement. We are very excited to be launching and want to make a great first impression. We will be conducting workshops and seminars (from government level to the hardware store owners) and we want our business card to give us the strong, confident introduction that we need.

Target Market(s)

construction; builders; engineers; home owners

Industry/Entity Type

Construction

Contact Information for Business Card

Marisol Depree
CEO
cell # 1 555 4180736
Ground floor,Lindell Plaza Suite 2734
George Town,Grand Cayman
Cayman Islands,KY1-4823
EMAIL: m.depree@drvventuresinc.example
web site drvventuresinc.example

COMPANY: skype info drv.ventures.example

second card
Yvette Brannock-Depree
CFO
CELL# 1 555 607 3941
George Town,Grand Cayman
Cayman Islands,KY1-4823
EMAIL: y.brannockdepree@drvventuresinc.example
website drvventuresinc.example

Requirements
Must have
• Business cards must display BOTH logos - DRV is the company and TORVAN SUPPLIES is the brand.

```html
<!DOCTYPE html>
<html lang="en">
<head>
<meta charset="utf-8">
<title>DRV Ventures Inc. – Business Card</title>
<link rel="stylesheet" href="https://fonts.googleapis.com/css2?family=Source+Sans+3:wght@400;600;700&display=swap">
<style>
  :root {
    --maroon: #6b1116;
    --paper: #f5f5f3;
    --ink: #565656;
    --ink-dark: #1c1c1c;
    --backdrop: #e4e4e4;
    --white: #ffffff;
  }
  * { box-sizing: border-box; margin: 0; padding: 0; }
  html, body {
    width: 1105px;
    height: 1200px;
    overflow: hidden;
    background: var(--backdrop);
    font-family: "Source Sans 3", Arial, sans-serif;
  }
  .card {
    position: absolute;
    left: 180px;
    width: 746px;
    height: 425px;
  }
  .card--front { top: 120px; background: var(--paper); color: var(--ink); }
  .card--back  { top: 640px; background: var(--maroon); color: var(--white); }

  .name-band {
    position: absolute;
    left: 0; top: 28px;
    width: 438px; height: 105px;
    background: var(--maroon);
    color: var(--white);
    padding: 24px 0 0 28px;
  }
  .name-band__name { font-size: 27px; font-weight: 600; line-height: 1.1; }
  .name-band__title { font-size: 19px; font-weight: 400; line-height: 1.3; }

  .company-mark {
    position: absolute;
    left: 441px; top: 28px;
    height: 105px;
    display: flex;
    align-items: center;
    gap: 12px;
  }
  .company-mark__square {
    width: 109px; height: 105px;
    background: var(--maroon);
  }
  .company-mark__name {
    font-size: 27px;
    font-weight: 700;
    line-height: 1.05;
    color: var(--ink-dark);
  }

  .address {
    position: absolute;
    left: 28px; bottom: 22px;
    font-size: 20px;
    line-height: 27px;
  }
  .contact {
    position: absolute;
    right: 28px; bottom: 22px;
    font-size: 20px;
    line-height: 27px;
    text-align: right;
  }
  .contact__label { color: var(--maroon); font-weight: 700; }

  .brand-mark {
    position: absolute;
    left: 0; right: 0; top: 120px;
    display: flex;
    flex-direction: column;
    align-items: center;
    gap: 18px;
  }
  .brand-mark__circle {
    width: 96px; height: 96px;
    border-radius: 50%;
    background: #e9e3e3;
  }
  .brand-mark__name {
    font-size: 30px;
    font-weight: 700;
    letter-spacing: 4px;
    color: #e9e3e3;
  }
  .back-url {
    position: absolute;
    left: 0; right: 0; top: 376px;
    text-align: center;
    font-size: 20px;
    color: #eeeeee;
  }
</style>
</head>
<body>
  <section class="card card--front">
    <div class="name-band">
      <div class="name-band__name">Marisol Depree</div>
      <div class="name-band__title">CEO</div>
    </div>
    <div class="company-mark">
      <div class="company-mark__square"></div>
      <div class="company-mark__name">DRV<br>Ventures Inc.</div>
    </div>
    <address class="address" style="font-style: normal;">
      Ground floor<br>
      Lindell Plaza Suite 2734<br>
      George Town,Grand Cayman<br>
      Cayman Islands,KY1-4823
    </address>
    <div class="contact">
      <div><span class="contact__label">Mobile:</span>1 555 4180736</div>
      <div>m.depree@drvventuresinc.example</div>
      <div>www.drvventuresinc.example</div>
    </div>
  </section>

  <section class="card card--back">
    <div class="brand-mark">
      <div class="brand-mark__circle"></div>
      <div class="brand-mark__name">TORVAN SUPPLIES</div>
    </div>
    <div class="back-url">www.drvventuresinc.example</div>
  </section>
</body>
</html>
```